Web Design For Marlow Pool Service

We are working with a company that wants a website for their pool service. Some sites to use for content/competitors and inspiration:
https://sacramento.brightwaterpoolco.example/builder/newbuild/repair/ppc
https://hollowbrookpoolcareplus.example/
https://lakemontpoolservice.example/
https://www.dravenspoolresurfacing.example/pool-renovation-ga/
Thank you for taking the time to consider designing a website for us. We are web developers based in Stockton, CA, USA. Most of our projects go through the same process. Understanding this process may help you win a project with us. We custom-code all of our websites in-house. We don’t have any requirements as to what tools you use for your design, but we prefer Figma files. For any design that we label as four-stars, we send it to the client for review. The client picks the final design they want us to use. Once we complete this process, we will continue to show additional clients all the four-star sites and purchase them later. Your designs will have multiple chances to sell. For better chances of success, we ask that you follow these guidelines.
IMAGES:
If you use any images or icons in the design, we ask that you have a link to the asset so we can purchase the image/icon. Most of the designs we submit do not have the customer’s images on them unless they have some great images. Be creative; show us the feeling you are trying to portray with your image choices. Use any royalty-free site you choose. We subscribe to Adobe and mainly use their images, but we can purchase images outside of Adobe. PLEASE NOTE: we will not submit designs to clients with watermarks on the images.
FONTS:
We ask that you identify the fonts used in the design. This can be done in a message if you want. We typically use Google Fonts and Adobe Fonts.
CONTENT:
We're always open to different content and ideas. We often submit designs with stock images so the client can see our vision. We typically take pictures after the website launch to use their images with our vision. Lorem Ipsum is fine for paragraphs, but we ask that you write the headers in correct English. We want to be able to show the vision and identify the sections of the website.
INSPIRATION:
We typically add a couple of links in the brief of websites we like to help you get started in your design.
REVISIONS:
We do not often ask for revisions of the designs unless we see something in the design that may not appeal to the client. If there are slight changes that we want to make, we do that in the development process.
FEEDBACK:
We rarely give feedback on designs during the design process. We are working on many website projects and do not have the time to provide feedback. We usually respond if your request is well thought out and asks specific questions, but a note asking “feedback, please” usually goes unanswered.
Number of Pages Required
1 page
Look and feel
Each slider illustrates characteristics of the customer's brand and the style your logo design should communicate.

```html
<!DOCTYPE html>
<html lang="en">
<head>
<meta charset="utf-8">
<title>Marlow Pool Service</title>
<link href="https://fonts.googleapis.com/css2?family=Cinzel:wght@500;600;700&family=Lato:wght@400;700&display=swap" rel="stylesheet">
<style>
:root{
  --navy:#0c2b66;
  --blue:#1565c8;
  --bright:#1d74d6;
  --sky:#2f9bf0;
  --ice:#dcecfc;
  --ink:#2a2f3a;
  --muted:#4b5260;
  --white:#ffffff;
  --star:#f7c238;
}
*{box-sizing:border-box;margin:0;padding:0}
html,body{width:1200px;height:3819px;overflow:hidden}
body{position:relative;background:var(--white);font-family:'Lato',sans-serif;color:var(--ink)}
.abs{position:absolute}
.serif{font-family:'Cinzel',serif}

/* hero */
.hero{left:0;top:0;width:1200px;height:566px;background:linear-gradient(180deg,#0d2f70,#0b2862)}
.brand{color:var(--white);font-family:'Cinzel',serif;font-weight:600;letter-spacing:1px;white-space:nowrap}
.brand small{display:block;font-weight:600}
.header-brand{left:113px;top:36px;font-size:26px;line-height:1}
.header-brand small{font-size:15px;letter-spacing:3px;margin-left:30px;margin-top:1px}
.nav{left:570px;top:40px;display:flex;gap:21px;font-size:15px;color:#dfe8f7}
.nav a{color:inherit;text-decoration:none}
.nav a.active{color:var(--white);font-weight:700}
.quote-btn{left:945px;top:30px;width:143px;height:40px;border:2px solid var(--white);border-radius:20px;color:var(--white);font-size:15px;display:flex;align-items:center;justify-content:center}
.hero-main{left:111px;top:212px;width:475px;height:325px;background:linear-gradient(150deg,#2fb6c9,#127a9e 70%,#0f5f84)}
.hero-title{left:156px;top:118px;color:var(--white);font-size:58px;line-height:67px;font-weight:500}
.hero-card{color:var(--white);font-family:'Cinzel',serif;font-size:25px;line-height:33px;font-weight:600}
.card-a{left:608px;top:104px;width:229px;height:376px;background:linear-gradient(180deg,#3b9be0,#1a62b8)}
.card-b{left:860px;top:159px;width:228px;height:378px;background:linear-gradient(180deg,#3ba6d8,#2270c4 55%,#1a5cb0)}
.hero-card span{position:absolute;left:26px}
.arrow{position:absolute;left:26px}

/* section headings */
.section-title{font-family:'Cinzel',serif;font-weight:700;font-size:46px;color:var(--bright);letter-spacing:.5px;white-space:nowrap}

/* about */
.about-img1{left:111px;top:653px;width:366px;height:472px;background:linear-gradient(180deg,#4a9fe8,#5db0e6 50%,#7aa35a 80%,#49b4d8)}
.about-img2{left:285px;top:890px;width:296px;height:293px;background:var(--white);padding:6px}
.about-img2 div{width:100%;height:100%;background:linear-gradient(180deg,#6aa34c,#d46b9a 40%,#2ba8d8 75%,#60c6ea)}
.about-text{left:657px;top:812px;width:432px;font-size:14px;line-height:28px;color:var(--muted)}
.about-text strong{display:block;color:var(--ink);font-size:16px;margin-bottom:16px}
.about-text p{margin-bottom:14px}
.pill{height:38px;border-radius:19px;background:var(--blue);color:var(--white);font-size:14px;display:flex;align-items:center;justify-content:center}

/* services */
.wave-band{height:18px;background:linear-gradient(90deg,transparent,#cfe4f8 20%,#d8eafa 80%,transparent)}
.svc{top:1433px;width:305px;height:370px}
.svc .bg{position:absolute;left:0;top:60px;width:305px;height:310px;background:linear-gradient(180deg,#ffffff,#cfe5fb);border-radius:150px 150px 0 0}
.svc .pic{position:absolute;left:36px;top:0;width:232px;height:232px;border-radius:50%;border:2px solid var(--bright)}
.svc .icon{position:absolute;left:112px;top:182px;width:80px;height:80px;border-radius:50%;background:var(--white);display:flex;align-items:center;justify-content:center;box-shadow:0 2px 6px rgba(0,0,0,.08)}
.svc h3{position:absolute;left:0;top:280px;width:305px;text-align:center;font-weight:400;font-size:21px;line-height:30px;color:#555b66}

/* why */
.why{left:0;top:1963px;width:1200px;height:646px;background:linear-gradient(180deg,#1260c4,#1873d8 60%,#2a8de8)}
.why-lead{left:111px;top:2178px;width:440px;color:var(--white);font-weight:700;font-size:14px;line-height:28px}
.why-list{left:111px;top:2262px;width:460px;list-style:none;color:#eaf3ff;font-size:14px;line-height:28px}
.why-list li{position:relative;padding-left:31px}
.why-list svg{position:absolute;left:0;top:7px}
.why-img1{left:697px;top:2045px;width:391px;height:470px;background:linear-gradient(180deg,#8fd4f0,#3aa3e0 45%,#1e72c4)}
.why-frame{left:611px;top:2250px;width:296px;height:290px;background:#0e4fa8}
.why-img2{left:611px;top:2267px;width:280px;height:283px;background:linear-gradient(180deg,#5cc3ec,#2e8fd6)}

/* testimonials */
.form{left:117px;top:2840px;width:356px;height:516px;background:#0d55b0;box-shadow:0 10px 30px rgba(0,0,0,.15);padding:44px 36px 0}
.form h3{color:var(--white);font-size:35px;font-weight:700;letter-spacing:-.5px}
.form p{color:#dbe7fa;font-size:13px;line-height:19px;margin:10px 0 18px}
.field{height:40px;background:var(--white);margin-bottom:27px;font-size:11px;color:#444;padding:0 18px;display:flex;align-items:center}
.form .send{height:40px;border-radius:20px;background:var(--sky);color:var(--white);font-size:15px;display:flex;align-items:center;justify-content:center;margin-top:-2px;margin-left:-4px;margin-right:-4px}
.review{left:528px;width:560px;height:245px;background:var(--white);box-shadow:0 4px 18px rgba(0,0,0,.12)}
.review .avatar{position:absolute;left:41px;top:33px;width:102px;height:102px;border-radius:50%;background:linear-gradient(180deg,#4b6878,#2f4858)}
.review .qmark{position:absolute;left:52px;top:120px;font-family:Georgia,serif;font-size:120px;color:#cfe2f8;line-height:1}
.review h4{position:absolute;left:166px;top:42px;color:var(--blue);font-size:17px;font-weight:700}
.review .stars{position:absolute;left:166px;top:68px;color:var(--star);font-size:15px;letter-spacing:1px}
.review p{position:absolute;left:166px;top:101px;width:366px;font-size:14px;line-height:28px;color:var(--muted)}
.review .corner{position:absolute;right:0;bottom:0;width:22px;height:18px;background:#8eb8ea;border-radius:8px 0 0 0}

/* footer */
.footer{left:0;top:3465px;width:1200px;height:354px;background:linear-gradient(180deg,#0d2f70,#0a2763)}
.footer-brand{left:117px;top:3560px;font-size:46px;line-height:1}
.footer-brand small{font-size:27px;letter-spacing:5px;margin-left:48px;margin-top:-2px}
.socials{left:137px;top:3645px;display:flex;gap:10px}
.socials span{width:30px;height:30px;border:1.5px solid var(--white);border-radius:50%}
.fcol{color:var(--white);font-size:14px;line-height:26px}
.fcol h5{font-size:15px;font-weight:700;margin-bottom:22px;position:relative}
.fcol h5::after{content:"";position:absolute;left:0;bottom:-8px;width:60px;height:2px;background:var(--sky)}
.contact-row{position:relative;padding-left:32px;margin-bottom:18px}
.contact-row svg{position:absolute;left:0;top:5px}
.copy{left:0;top:3760px;width:1200px;text-align:center;color:var(--white);font-size:14px}
</style>
</head>
<body>

<!-- HERO -->
<header class="abs hero"></header>
<div class="abs brand header-brand">Marlow<small>Pool Service</small></div>
<nav class="abs nav"><a class="active" href="#">Home</a><a href="#">Services</a><a href="#">Products</a><a href="#">About</a><a href="#">Contact</a></nav>
<div class="abs quote-btn">Get a Quote</div>
<div class="abs hero-main" role="img" aria-label="Man floating on his back in a turquoise pool"></div>
<h1 class="abs serif hero-title">Crafting<br>Your Pool<br>Paradise</h1>
<div class="abs hero-card card-a" role="img" aria-label="Smiling child swimming in blue pool water">
  <span style="top:240px">Work with<br>the best</span>
  <svg class="arrow" style="top:320px" width="20" height="26" viewBox="0 0 20 26"><path d="M10 1v23M2 16l8 8 8-8" fill="none" stroke="#fff" stroke-width="2"/></svg>
</div>
<div class="abs hero-card card-b" role="img" aria-label="Legs dangling into a tiled pool from above the waterline">
  <span style="top:238px">What<br>we do</span>
  <svg class="arrow" style="top:318px" width="20" height="26" viewBox="0 0 20 26"><path d="M10 1v23M2 16l8 8 8-8" fill="none" stroke="#fff" stroke-width="2"/></svg>
</div>

<!-- ABOUT -->
<div class="abs about-img1" role="img" aria-label="Child jumping into a pool with a pink float"></div>
<div class="abs about-img2" role="img" aria-label="Children splashing into a pool with flamingo floats"><div></div></div>
<h2 class="abs section-title" style="left:688px;top:715px">About Us</h2>
<div class="abs about-text">
  <strong>Ut enim ad minima veniam, quis nostrum exercitationem.</strong>
  <p>Lorem ipsum dolor sit amet, consectetur adipiscised do eiusimod tempor incididunt ut labore et dolore magna aliqua.</p>
  <p>Sed ut perspiciatis unde omnis iste natus error sit voluptatem accusan tium doloremque laudantium, totam remaperiam, eaque ipsa quae ab illo invenre veritatis et quasi architecto beatae vitae dicta sunt explimo enim ipsam voluptatem quia voluptas.</p>
</div>
<div class="abs pill" style="left:657px;top:1057px;width:143px">Learn More</div>

<!-- SERVICES -->
<div class="abs wave-band" style="left:0;top:1318px;width:390px"></div>
<h2 class="abs section-title" style="left:454px;top:1305px">Our Services</h2>

<div class="abs svc" style="left:111px">
  <div class="bg"></div>
  <div class="pic" role="img" aria-label="Garden pool with palms and a swan float" style="background:linear-gradient(180deg,#3c6e2e,#6a9a4c 45%,#3aa6c8)"></div>
  <div class="icon"><svg width="40" height="34" viewBox="0 0 40 34" fill="none" stroke="#1d74d6" stroke-width="1.8"><path d="M8 26V6a4 4 0 0 1 8 0M20 26V6a4 4 0 0 1 8 0M8 12h12M8 19h12"/><path d="M2 29c4 0 4-2 8-2s4 2 8 2 4-2 8-2 4 2 8 2 4-2 6-2"/></svg></div>
  <h3>Swimming Pool<br>Services</h3>
</div>
<div class="abs svc" style="left:448px">
  <div class="bg"></div>
  <div class="pic" role="img" aria-label="Robotic pool cleaner on a pool floor" style="background:linear-gradient(160deg,#9ed8f2,#3b94d2)"></div>
  <div class="icon"><svg width="40" height="36" viewBox="0 0 40 36" fill="none" stroke="#1d74d6" stroke-width="1.8"><rect x="8" y="14" width="20" height="12"/><path d="M30 2 18 20M14 14v-4h8"/><path d="M2 31c4 0 4-2 8-2s4 2 8 2 4-2 8-2 4 2 8 2"/></svg></div>
  <h3>Pool Cleaning<br>Service</h3>
</div>
<div class="abs svc" style="left:784px">
  <div class="bg"></div>
  <div class="pic" role="img" aria-label="Technician repairing pool pump equipment" style="background:linear-gradient(160deg,#8a96a6,#d8502e 45%,#2d3e5c)"></div>
  <div class="icon"><svg width="40" height="38" viewBox="0 0 40 38" fill="none" stroke="#1d74d6" stroke-width="1.8"><path d="M10 4l16 16M26 4 10 20"/><path d="M6 24h28l-3 10H9z"/><path d="M8 30c3 0 3-1.5 6-1.5s3 1.5 6 1.5 3-1.5 6-1.5"/></svg></div>
  <h3>Swimming Pool<br>Repair</h3>
</div>
<div class="abs pill" style="left:529px;top:1860px;width:142px">Learn More</div>

<!-- WHY CHOOSE US -->
<section class="abs why"></section>
<h2 class="abs section-title" style="left:157px;top:2077px;color:#fff">Why Choose Us</h2>
<p class="abs why-lead">Lorem ipsum dolor sit amet, consectetur adipiscised do eiimod tempor incididunt ut labore et dolore magna aliqua.</p>
<ul class="abs why-list">
  <li><svg width="13" height="13" viewBox="0 0 14 14"><circle cx="7" cy="7" r="6" fill="none" stroke="#fff" stroke-width="1.5"/><path d="M4 7l2 2 4-4" fill="none" stroke="#fff" stroke-width="1.5"/></svg>Sed ut perspiciatis unde omnis iste natus error sit voluptatem accusan tium doloremque laudantium.</li>
  <li><svg width="13" height="13" viewBox="0 0 14 14"><circle cx="7" cy="7" r="6" fill="none" stroke="#fff" stroke-width="1.5"/><path d="M4 7l2 2 4-4" fill="none" stroke="#fff" stroke-width="1.5"/></svg>Totam remaperiam, eaque ipsa quae ab illo invenre</li>
  <li><svg width="13" height="13" viewBox="0 0 14 14"><circle cx="7" cy="7" r="6" fill="none" stroke="#fff" stroke-width="1.5"/><path d="M4 7l2 2 4-4" fill="none" stroke="#fff" stroke-width="1.5"/></svg>Veritatis et quasi architecto beatae vitae dicta sunt</li>
  <li><svg width="13" height="13" viewBox="0 0 14 14"><circle cx="7" cy="7" r="6" fill="none" stroke="#fff" stroke-width="1.5"/><path d="M4 7l2 2 4-4" fill="none" stroke="#fff" stroke-width="1.5"/></svg>Explimo enim ipsam voluptatem quia voluptas.</li>
  <li><svg width="13" height="13" viewBox="0 0 14 14"><circle cx="7" cy="7" r="6" fill="none" stroke="#fff" stroke-width="1.5"/><path d="M4 7l2 2 4-4" fill="none" stroke="#fff" stroke-width="1.5"/></svg>Sed ut perspiciatis unde omnis iste natus error sit voluptatem accusan tium doloremque laudantium.</li>
  <li><svg width="13" height="13" viewBox="0 0 14 14"><circle cx="7" cy="7" r="6" fill="none" stroke="#fff" stroke-width="1.5"/><path d="M4 7l2 2 4-4" fill="none" stroke="#fff" stroke-width="1.5"/></svg>Totam remaperiam, eaque ipsa quae ab illo invenre</li>
</ul>
<div class="abs why-img1" role="img" aria-label="Boy with goggles swimming underwater"></div>
<div class="abs why-frame"></div>
<div class="abs why-img2" role="img" aria-label="Girl with pink goggles holding her nose underwater"></div>

<!-- TESTIMONIALS -->
<h2 class="abs section-title" style="left:454px;top:2717px">Testimonials</h2>
<div class="abs wave-band" style="left:830px;top:2740px;width:370px"></div>

<form class="abs form">
  <h3>Get a Quote Today</h3>
  <p>Connect with us and lets discuss your<br>pool service options.</p>
  <div class="field">Your Name</div>
  <div class="field">Email</div>
  <div class="field">Phone Number</div>
  <div class="field">Location</div>
  <div class="send">Learn More</div>
</form>

<article class="abs review" style="top:2842px">
  <div class="avatar" role="img" aria-label="Customer portrait"></div>
  <div class="qmark">&ldquo;</div>
  <h4>HARPER L</h4>
  <div class="stars">★★★★★</div>
  <p>Sed ut perspiciats unde omnis iste error sit oluptatem accusantium doloreudantium, tot rem aperiam, eaque ipsa quae abuasi architec beatae vitae dicta sunt expli cabocusantium doloreudantium totam.</p>
  <div class="corner"></div>
</article>
<article class="abs review" style="top:3116px">
  <div class="avatar" role="img" aria-label="Customer portrait"></div>
  <div class="qmark">&ldquo;</div>
  <h4>HARPER L</h4>
  <div class="stars">★★★★★</div>
  <p>Sed ut perspiciats unde omnis iste error sit oluptatem accusantium doloreudantium, tot rem aperiam, eaque ipsa quae abuasi architec beatae vitae dicta sunt expli cabocusantium doloreudantium totam.</p>
  <div class="corner"></div>
</article>

<!-- FOOTER -->
<footer class="abs footer"></footer>
<div class="abs brand footer-brand">Marlow<small>Pool Service</small></div>
<div class="abs socials"><span></span><span></span><span></span><span></span><span></span></div>

<div class="abs fcol" style="left:458px;top:3525px;width:260px">
  <h5>CONTACT INFO</h5>
  <div class="contact-row"><svg width="14" height="18" viewBox="0 0 14 18"><path d="M7 17s6-6.5 6-10A6 6 0 0 0 1 7c0 3.5 6 10 6 10z" fill="#2f9bf0"/><circle cx="7" cy="7" r="2.2" fill="#0c2b66"/></svg>Marlow Pool Services,<br>Address Comes Here</div>
  <div class="contact-row"><svg width="15" height="15" viewBox="0 0 16 16"><path d="M3 1l3 3-2 2c1 2.5 3.5 5 6 6l2-2 3 3-2 2C7 15 1 9 1 3z" fill="#2f9bf0"/></svg>+1888-888-8888</div>
  <div class="contact-row"><svg width="16" height="12" viewBox="0 0 16 12"><rect width="16" height="12" rx="1" fill="#2f9bf0"/><path d="M1 1l7 6 7-6" fill="none" stroke="#0c2b66" stroke-width="1.3"/></svg>info@marlowpoolservice.com</div>
</div>
<div class="abs fcol" style="left:767px;top:3525px">
  <h5>QUICK LINKS</h5>
  Home<br>About<br>Services<br>Products<br>Contact
</div>
<div class="abs fcol" style="left:955px;top:3525px">
  <h5>OTHER LINKS</h5>
  Terms &amp; Conditions<br>Privacy Policy<br>FAQ<br>Cookies<br>Support
</div>
<div class="abs copy">2024 Marlow Pool Services. All Rights Reserved.</div>

</body>
</html>
```